Business Card Re-Design/Update

We'd like to update out business cards. I've included our current "Style guide" which has the colour scheme of the organisation in it. I've also included the branding files with logos etc in them.

I've also included a copy of one of our existing cards so that you can see how ugly/dated they look. I'd like a fresh modern corporate look.

Target Market(s)

These are for our clients, potential clients, industry contacts - like all business cards

Contact Information for Business Card

Name
Position
Company Address - Level 1, 47 Fernby Street, Carlow Qld 4072
Direct Phone
mobile
Email
Website -www.korvalit.com.au
Logo

Colors

Designer to choose colors to be used in the design.

Requirements
Must have
• Main Logo
• Cards will need to be editable to be able to personalize them for each new employee.
Nice to have
• The MapOut, ShipWell, KeepSteady would be okay to have if they can be sensibly and professionally added to the look without detracting from the main imagery.
• Maybe they could go on the back of the card? will leave this to your creative discretion as to whether/where they fit.
Should not have
• Should not have decorative or script fonts

```html
<!DOCTYPE html>
<html lang="en">
<head>
<meta charset="utf-8">
<title>korvalIT business card</title>
<link rel="stylesheet" href="https://fonts.googleapis.com/css2?family=Lato:wght@300;400;700;900&display=swap">
<style>
  :root {
    --backdrop: #e4e5e7;
    --paper: #ffffff;
    --ink: #1e1e1e;
    --ink-soft: #4a4a4a;
    --brand-red: #d71f27;
    --card-dark: #1b1b1b;
    --card-dark-2: #262626;
    --rule: #9a9a9a;
  }
  * { box-sizing: border-box; margin: 0; padding: 0; }
  html, body {
    width: 1200px; height: 1200px; overflow: hidden;
    background: var(--backdrop);
    font-family: "Lato", Arial, sans-serif;
    color: var(--ink);
  }
  .sheet {
    width: 1200px; height: 1200px;
    display: flex; flex-direction: column; align-items: center; justify-content: center;
    gap: 60px;
  }
  .card {
    position: relative;
    width: 900px; height: 500px;
    border-bottom: 8px solid var(--brand-red);
    box-shadow: 0 10px 28px rgba(0,0,0,0.12);
    overflow: hidden;
  }

  /* Front */
  .card--front { background: var(--paper); }
  .brand {
    position: absolute; left: 70px; top: 50%;
    transform: translateY(-50%);
    display: flex; align-items: center; gap: 22px;
  }
  .brand__mark {
    width: 58px; height: 58px; background: var(--brand-red);
  }
  .brand__name {
    font-weight: 900; font-size: 72px; letter-spacing: -1px;
    color: var(--ink); line-height: 1;
  }
  .details {
    position: absolute; left: 560px; top: 70px;
    padding-left: 26px;
    border-left: 1.5px solid var(--rule);
    height: 270px;
  }
  .details__name {
    font-weight: 700; font-size: 30px; color: var(--brand-red); line-height: 1.1;
  }
  .details__role, .details__address {
    font-weight: 400; font-size: 17px; color: var(--ink-soft); line-height: 1.55;
  }
  .details__role { margin-top: 6px; }
  .details__address { margin-bottom: 10px; }
  .contact { list-style: none; }
  .contact__item {
    display: flex; align-items: center; gap: 12px;
    font-size: 17px; color: var(--ink-soft); line-height: 1.6;
  }
  .contact__icon { width: 15px; height: 15px; flex: none; fill: var(--brand-red); }

  /* Back */
  .card--back { background: var(--card-dark); }
  .back-texture {
    position: absolute; inset: 0;
    background: linear-gradient(135deg, var(--card-dark-2), var(--card-dark) 60%);
  }
  .services {
    position: absolute; left: 0; right: 0; top: 250px;
    display: flex; justify-content: center; gap: 34px;
    list-style: none;
    font-weight: 400; font-size: 30px; color: #ffffff;
  }
  .services__item { display: flex; align-items: center; gap: 12px; }
  .services__item::before {
    content: ""; width: 7px; height: 7px; border-radius: 50%; background: var(--brand-red);
  }
  .back-mark {
    position: absolute; right: 70px; bottom: 70px;
    width: 50px; height: 50px; background: var(--brand-red);
  }
</style>
</head>
<body>
<main class="sheet">

  <section class="card card--front" aria-label="Card front">
    <div class="brand">
      <span class="brand__mark"></span>
      <span class="brand__name">korvalIT</span>
    </div>

    <div class="details">
      <p class="details__name">Mara Ellison</p>
      <p class="details__role">Business Development Manager</p>
      <p class="details__address">Level 1, 47 Fernby Street<br>Carlow Qld 4072</p>
      <ul class="contact">
        <li class="contact__item">
          <svg class="contact__icon" viewBox="0 0 16 16" aria-hidden="true"><path d="M3.2 1.5l2.4 2.6-1.3 1.8c.9 2 2.5 3.6 4.6 4.6l1.8-1.3 2.6 2.4-1.4 2.3C6.4 13.8 2.2 9.6 1 3z"/></svg>
          +61 (07) 3480 2716
        </li>
        <li class="contact__item">
          <svg class="contact__icon" viewBox="0 0 16 16" aria-hidden="true"><path d="M4 1h8v4H4z M1 6h14v6h-3v3H4v-3H1z M5.5 10v3.5h5V10z"/></svg>
          +61 (07) 3480 2716
        </li>
        <li class="contact__item">
          <svg class="contact__icon" viewBox="0 0 16 16" aria-hidden="true"><path d="M1 3h14v10H1z M2 4l6 5 6-5" stroke="#fff" stroke-width="1.2"/></svg>
          info@korvalit.com.au
        </li>
        <li class="contact__item">
          <svg class="contact__icon" viewBox="0 0 16 16" aria-hidden="true"><circle cx="8" cy="8" r="7"/><path d="M1 8h14M8 1c-3 3.5-3 10.5 0 14M8 1c3 3.5 3 10.5 0 14" stroke="#fff" stroke-width="1" fill="none"/></svg>
          www.korvalit.com.au
        </li>
      </ul>
    </div>
  </section>

  <section class="card card--back" aria-label="Card back">
    <div class="back-texture" role="img" aria-label="Subtle dark tone-on-tone geometric pattern"></div>
    <ul class="services">
      <li class="services__item">The MapOut</li>
      <li class="services__item">ShipWell</li>
      <li class="services__item">KeepSteady</li>
    </ul>
    <span class="back-mark"></span>
  </section>

</main>
</body>
</html>
```